** Wanted ** Wordpress web design for scaffolding rental and construction company

We need a website design and must be functional to show a basic overview of what our company offers as a service. We have a domain name and a logo but we need web design. This web site should have another scaffolding rental page for construction and renovation as well as a quote section where customers can enter their personal information and also upload photos. The site% 26quot; www.brindlework.com% 26quot; should be intuitive, clear and classy ... The logo must be found on the site in several ways.

Target Market(s)

Professional and no professional

Coding

Coded - Design and coding required

Number of Pages Required

3 page

Font styles to use
Serif
Sans Serif
Decorative
Script

Requirements
Must have
• Our logo
Nice to have
• Slogan:% 26quot; The height% 26 # 224; port% 26 # 233; e hand% 26quot;

```html
<!DOCTYPE html>
<html lang="en">
<head>
<meta charset="utf-8">
<title>Brindlework – Scaffolding Rental and Construction</title>
<link rel="stylesheet" href="https://fonts.googleapis.com/css2?family=Roboto:wght@300;400;500;700;900&display=swap">
<style>
:root{
  --blue:#1a7fd6;
  --blue-dark:#0f5fae;
  --orange:#f47b20;
  --ink:#1c1c1c;
  --text:#444;
  --black:#0b0b0c;
  --white:#fff;
}
*{box-sizing:border-box;margin:0;padding:0}
html,body{width:1200px;height:4959px;overflow:hidden}
body{position:relative;font-family:"Roboto",sans-serif;color:var(--text);background:#fff}
.abs{position:absolute}
.btn{position:absolute;background:var(--orange);color:#fff;font-weight:700;font-size:16px;display:flex;align-items:center;justify-content:center;gap:8px;text-transform:uppercase}
.btn svg{width:16px;height:16px}

/* hero */
.hero{position:absolute;left:0;top:0;width:1200px;height:780px;clip-path:polygon(0 0,100% 0,100% 690px,50% 780px,0 690px);
  background:
    radial-gradient(ellipse 260px 200px at 880px 180px,rgba(232,170,40,.85),rgba(232,170,40,0) 70%),
    radial-gradient(ellipse 220px 260px at 720px 520px,rgba(226,120,40,.8),rgba(226,120,40,0) 70%),
    radial-gradient(ellipse 300px 380px at 1050px 420px,rgba(70,78,88,.7),rgba(70,78,88,0) 75%),
    linear-gradient(90deg,#4a3f33 0%,#6e6050 30%,#5b5247 52%,#3f3c3a 70%,#55504a 100%)}
.hero-shade{position:absolute;inset:0;background:linear-gradient(90deg,rgba(0,0,0,.5) 0%,rgba(0,0,0,.25) 45%,rgba(0,0,0,0) 70%)}
.brand{position:absolute;left:143px;top:88px;width:196px;height:40px;border:2px solid var(--blue);display:flex;align-items:center;justify-content:center;color:#fff;font-weight:700;font-size:17px;letter-spacing:2px}
.call{position:absolute;left:570px;top:34px;display:flex;gap:10px;align-items:center;color:#fff}
.call .ic{width:36px;height:36px;border-radius:50%;background:#fff;display:flex;align-items:center;justify-content:center}
.call small{display:block;font-size:14px;line-height:16px}
.call b{font-size:19px;line-height:24px}
.search{position:absolute;left:792px;top:38px;width:262px;height:34px;background:#fff;border-radius:17px;font-size:12px;color:#999;padding:10px 18px}
.search svg{position:absolute;right:14px;top:11px}
.nav{position:absolute;left:400px;top:98px;display:flex;gap:28px;color:#fff;font-weight:700;font-size:17px}
.nav .on{border:2px solid var(--blue);padding:1px 10px;margin-top:-3px}
.hero-badge{position:absolute;left:144px;top:273px;width:380px;height:76px;border:3px solid var(--blue);display:flex;align-items:center;justify-content:center;color:#fff;font-weight:700;font-size:34px;letter-spacing:5px}
.hero-title{position:absolute;left:143px;top:372px;color:#fff;font-weight:700;font-size:49px;line-height:57px;text-transform:uppercase}
.arrow-btn{position:absolute;top:372px;width:38px;height:38px;border-radius:50%;background:rgba(0,0,0,.55);border:1px solid rgba(255,255,255,.4);display:flex;align-items:center;justify-content:center}

/* welcome */
.welcome-art{position:absolute;left:150px;top:834px;width:400px;height:400px}
.welcome-kicker{position:absolute;left:610px;top:836px;font-size:24px;color:#333}
.welcome-title{position:absolute;left:610px;top:866px;font-size:38px;font-weight:700;color:var(--blue)}
.welcome-copy{position:absolute;left:610px;top:928px;width:450px;font-size:12.5px;line-height:24px;color:#555}

/* services */
.services{position:absolute;left:0;top:1279px;width:1200px;height:820px;clip-path:polygon(50% 0,100% 92px,100% 730px,50% 820px,0 730px,0 92px);
  background:
    radial-gradient(ellipse 500px 300px at 900px 650px,rgba(70,64,52,.6),rgba(0,0,0,0) 70%),
    radial-gradient(ellipse 400px 260px at 250px 700px,rgba(60,58,54,.5),rgba(0,0,0,0) 70%),
    linear-gradient(180deg,#141415,#0b0b0c 50%,#1d1b18)}
.section-title{position:absolute;width:1200px;text-align:center;font-size:40px;text-transform:uppercase}
.section-title b{font-weight:900}
.section-title span{font-weight:400}
.svc-photo{position:absolute;width:440px;height:226px}
.svc-card{position:absolute;width:440px;height:222px;border:4px solid var(--blue);color:#fff;text-align:center;padding:38px 38px 0}
.svc-card h3{font-size:16px;font-weight:700;margin-bottom:12px}
.svc-card p{font-size:13px;line-height:22px;color:#d8d8d8}
.svc-diamond{position:absolute;width:84px;height:84px}

/* blog */
.blog-title{position:absolute;left:143px;top:2148px;font-size:30px;font-weight:900;color:var(--ink)}
.blog-rule{position:absolute;left:143px;top:2192px;width:60px;height:3px;background:var(--blue-dark)}
.post-photo{position:absolute;left:143px;width:223px;height:170px}
.post-card{position:absolute;left:339px;width:264px;height:145px;background:#fff;box-shadow:0 2px 8px rgba(0,0,0,.12);padding:16px 18px}
.post-card h4{font-size:15px;font-weight:700;color:#222;margin-bottom:7px}
.post-meta{font-size:13px;color:var(--blue);display:flex;gap:18px;margin-bottom:7px}
.post-card p{font-size:13px;line-height:19px;color:#555}
.quote-bg{position:absolute;left:640px;top:2480px;width:560px;height:420px;
  background:linear-gradient(180deg,rgba(255,255,255,0),rgba(200,202,205,.55) 55%,rgba(170,172,175,.6))}
.quote{position:absolute;left:672px;top:2242px;width:382px;height:535px;border:5px solid var(--blue);background:#fff}
.quote h2{position:absolute;top:48px;width:100%;text-align:center;font-size:28px;font-weight:700;color:#222}
.field{position:absolute;left:36px;width:300px;height:38px;border:1px solid #bbb;font-size:12px;color:#555;padding:11px 14px}
.upload{position:absolute;right:0;top:0;width:144px;height:36px;background:#ddd;text-align:center;font-weight:700;font-size:13px;color:#333;line-height:36px}

/* team */
.team{position:absolute;left:0;top:2866px;width:1200px;height:684px;clip-path:polygon(50% 0,100% 81px,100% 601px,50% 684px,0 601px,0 81px);
  background:radial-gradient(ellipse 420px 360px at 820px 340px,#e8e9ea,rgba(232,233,234,0) 80%),linear-gradient(90deg,#b9bcbf 0%,#d2d4d6 45%,#dcdedf 100%)}
.team-photo{position:absolute;left:0;top:0;width:600px;height:684px;
  background:
    radial-gradient(circle 34px at 180px 220px,#1f66c9,rgba(31,102,201,0) 100%),
    radial-gradient(ellipse 120px 90px at 470px 390px,rgba(232,100,40,.85),rgba(232,100,40,0) 100%),
    radial-gradient(ellipse 110px 80px at 330px 250px,rgba(150,175,210,.8),rgba(150,175,210,0) 100%),
    radial-gradient(ellipse 80px 70px at 130px 570px,rgba(232,110,50,.7),rgba(232,110,50,0) 100%),
    linear-gradient(135deg,#9fa3a6 0%,#e7e7e5 35%,#d6d7d6 60%,#b4b7b9 100%)}
.role{position:absolute;width:146px;height:154px;background:#fff;box-shadow:0 2px 10px rgba(0,0,0,.15);text-align:center;padding-top:18px;font-size:17px;color:#333;line-height:21px}
.role .ico{width:58px;height:58px;border-radius:50%;margin:0 auto 10px;background:radial-gradient(circle at 40% 35%,#f9d68a,#eeae3e)}

/* projects */
.proj{position:absolute;width:298px;height:257px}
.proj-hover{position:absolute;left:451px;top:3744px;width:298px;height:257px;background:rgba(26,127,214,.9);color:#fff;text-align:center;padding:150px 24px 0}
.proj-hover h4{font-size:19px;font-weight:500;margin-bottom:8px;text-transform:uppercase}
.proj-hover p{font-size:13px;line-height:19px}
.site-fade{position:absolute;left:0;top:4060px;width:1200px;height:420px;background:linear-gradient(180deg,rgba(255,255,255,0),rgba(205,206,208,.6) 60%,rgba(180,182,184,.6))}

/* footer */
.footer{position:absolute;left:0;top:4449px;width:1200px;height:510px;background:var(--black);clip-path:polygon(0 81px,50% 0,100% 81px,100% 100%,0 100%)}
.foot-h{position:absolute;top:4556px;color:#fff;font-size:23px;font-weight:700;text-transform:uppercase}
.foot-t{position:absolute;color:#ddd;font-size:13.5px;line-height:20px}
.foot-links{position:absolute;left:909px;top:4610px;color:#ddd;font-size:13.5px;line-height:30px;list-style:none}
.subscribe{position:absolute;left:466px;top:4682px;width:366px;height:40px;background:#fff;border-radius:20px;font-size:12px;color:#777;padding:12px 20px}
.subscribe span{position:absolute;right:0;top:0;height:40px;width:118px;border-radius:20px;background:var(--blue);color:#fff;font-weight:700;text-align:center;line-height:40px}
.social{position:absolute;top:4740px;width:24px;height:24px;border-radius:50%;border:1px solid #aaa}
.copy{position:absolute;top:4896px;width:1200px;text-align:center;color:#ccc;font-size:13px}
</style>
</head>
<body>

<!-- hero -->
<section class="hero" role="img" aria-label="Aerial photo of construction workers in hard hats and orange vests tying steel reinforcement">
  <div class="hero-shade"></div>
</section>
<div class="brand">BRINDLEWORK</div>
<div class="call">
  <div class="ic"><svg width="18" height="18" viewBox="0 0 24 24"><path fill="#333" d="M6.6 10.8a15 15 0 006.6 6.6l2.2-2.2c.3-.3.7-.4 1-.2 1.1.4 2.3.6 3.6.6.6 0 1 .4 1 1V20c0 .6-.4 1-1 1A17 17 0 013 4c0-.6.4-1 1-1h3.5c.6 0 1 .4 1 1 0 1.3.2 2.5.6 3.6.1.3 0 .7-.2 1z"/></svg></div>
  <div><small>Call Now</small><b>+808 5550 0142</b></div>
</div>
<div class="search">Search here<svg width="12" height="12" viewBox="0 0 24 24"><circle cx="10" cy="10" r="7" fill="none" stroke="#999" stroke-width="2"/><path d="M15 15l6 6" stroke="#999" stroke-width="2"/></svg></div>
<nav class="nav"><span class="on">HOME</span><span>ABOUT US</span><span>OUR SERVICES</span><span>PROJECTS</span><span>BLOG</span><span>CONTACT</span></nav>
<div class="hero-badge">BRINDLEWORK</div>
<h1 class="hero-title">Scaffolding Rental<br>and Construction</h1>
<div class="btn" style="left:143px;top:505px;width:181px;height:44px">Learn More <svg viewBox="0 0 16 16"><path d="M2 8h11M9 4l4 4-4 4" stroke="#fff" stroke-width="2" fill="none"/></svg></div>
<div class="arrow-btn" style="left:58px"><svg width="12" height="12" viewBox="0 0 12 12"><path d="M8 1L3 6l5 5" stroke="#fff" stroke-width="1.5" fill="none"/></svg></div>
<div class="arrow-btn" style="left:1104px"><svg width="12" height="12" viewBox="0 0 12 12"><path d="M4 1l5 5-5 5" stroke="#fff" stroke-width="1.5" fill="none"/></svg></div>

<!-- welcome -->
<svg class="welcome-art" viewBox="0 0 400 400" role="img" aria-label="Diamond-shaped photo of a builder working on a construction site">
  <defs>
    <linearGradient id="wg" x1="0" y1="0" x2="1" y2="1"><stop offset="0" stop-color="#9cbcd3"/><stop offset=".45" stop-color="#5d84a3"/><stop offset="1" stop-color="#223f57"/></linearGradient>
    <radialGradient id="wl" cx=".6" cy=".45" r=".45"><stop offset="0" stop-color="#e8eef2" stop-opacity=".75"/><stop offset="1" stop-color="#e8eef2" stop-opacity="0"/></radialGradient>
  </defs>
  <polygon points="200,0 400,200 200,400 0,200" fill="url(#wg)"/>
  <polygon points="200,0 400,200 200,400 0,200" fill="url(#wl)"/>
</svg>
<div class="welcome-kicker">Welcome to</div>
<h2 class="welcome-title">BRINDLEWORK</h2>
<p class="welcome-copy">Sed ut perspiciatis unde omnis iste natus error sit voluptatem accusantium doloremque laudantium, totam rem aperiam, eaque ipsa quae ab illo inventore veritatis et quasi architecto beatae vitae dicta sunt explicabo. Nemo enim ipsam voluptatem quia voluptas sit aspernatur aut odit aut fugit, sed quia consequuntur magni dolores eos qui ratione voluptatem sequi nesciunt. Neque porro quisquam est, qui dolorem ipsum quia dolor sit amet, consectetur, adipisci velit, sed quia non numquam eius modi tempora incidunt ut labore et dolore magnam aliquam quaerat voluptatem. Ut enim ad minima veniam</p>
<div class="btn" style="left:610px;top:1177px;width:155px;height:38px;font-size:14px">Learn More <svg viewBox="0 0 16 16"><path d="M2 8h11M9 4l4 4-4 4" stroke="#fff" stroke-width="2" fill="none"/></svg></div>

<!-- services -->
<section class="services" role="img" aria-label="Dark photo of a construction site behind the services"></section>
<svg class="abs" style="left:0;top:1275px" width="1200" height="100"><polyline points="0,96 600,4 1200,96" fill="none" stroke="var(--blue)" stroke-width="5"/></svg>
<svg class="abs" style="left:0;top:2005px" width="1200" height="100"><polyline points="0,4 600,94 1200,4" fill="none" stroke="var(--blue-dark)" stroke-width="4"/></svg>
<h2 class="section-title" style="top:1375px;color:#fff"><b>OUR</b> <span>SERVICES</span></h2>
<div class="svc-photo" role="img" aria-label="Photo of steel scaffolding against a cloudy sky" style="left:143px;top:1489px;background:radial-gradient(ellipse 180px 80px at 120px 50px,#eef3f7,rgba(238,243,247,0) 80%),linear-gradient(180deg,#a9c1d4 0%,#8ea6b8 40%,#5e6e78 70%,#3d4346 100%)"></div>
<div class="svc-photo" role="img" aria-label="Photo of a worker in red overalls on a construction deck" style="left:607px;top:1489px;background:radial-gradient(ellipse 60px 90px at 330px 120px,rgba(214,40,40,.9),rgba(214,40,40,0) 100%),linear-gradient(180deg,#7fa9d0 0%,#a9c3d8 40%,#c8b497 65%,#8d7d68 100%)"></div>
<div class="svc-card" style="left:143px;top:1714px"><h3>SCAFFOLDING RENTAL</h3><p>Sed ut perspiciatis unde omnis iste natus error sit voluptatem accusantium doloremque laudantium, totam rem aperiam, eaque ipsa quae ab illo inventore veritatis et quasi architecto beatae vitae dicta sunt explicabo. Nemo enim ipsam voluptatem</p></div>
<div class="svc-card" style="left:607px;top:1714px"><h3>CONSTRUCTION</h3><p>Sed ut perspiciatis unde omnis iste natus error sit voluptatem accusantium doloremque laudantium, totam rem aperiam, eaque ipsa quae ab illo inventore veritatis et quasi architecto beatae vitae dicta sunt explicabo. Nemo enim ipsam voluptatem</p></div>
<svg class="svc-diamond" style="left:321px;top:1624px" viewBox="0 0 84 84">
  <polygon points="42,2 82,42 42,82 2,42" fill="var(--blue)"/><polygon points="42,8 76,42 42,76 8,42" fill="#fff"/>
  <g stroke="var(--blue)" stroke-width="2" fill="none"><rect x="28" y="28" width="28" height="28"/><path d="M28 42h28M28 28l28 14M56 28L28 42M28 42l28 14M56 42L28 56"/></g>
</svg>
<svg class="svc-diamond" style="left:785px;top:1624px" viewBox="0 0 84 84">
  <polygon points="42,2 82,42 42,82 2,42" fill="var(--blue)"/><polygon points="42,8 76,42 42,76 8,42" fill="#fff"/>
  <g stroke="var(--blue)" stroke-width="2.5" fill="none"><circle cx="42" cy="42" r="9"/><path d="M42 27v6M42 51v6M27 42h6M51 42h6M31.4 31.4l4.2 4.2M48.4 48.4l4.2 4.2M52.6 31.4l-4.2 4.2M35.6 48.4l-4.2 4.2"/></g>
</svg>

<!-- blog -->
<h2 class="blog-title">RECENT BLOG</h2>
<div class="blog-rule"></div>

<div class="post-photo" role="img" aria-label="Photo of a builder in a yellow hard hat reviewing plans" style="top:2244px;background:radial-gradient(ellipse 90px 70px at 60px 40px,#fbe2b0,rgba(251,226,176,0) 100%),radial-gradient(ellipse 50px 40px at 160px 90px,rgba(240,190,40,.9),rgba(240,190,40,0) 100%),linear-gradient(120deg,#e8a55a,#a27a58 60%,#d8d2cc)"></div>
<article class="post-card" style="top:2258px"><h4>NEMO ENIM IPSAM VOLUP</h4><div class="post-meta"><span>▦ Jan 25, 2020</span><span>◌ 2 comments</span></div><p>Sed ut perspiciatis unde omnis iste natus error sit vuptatem aum doloremque</p></article>

<div class="post-photo" role="img" aria-label="Photo of a worker on scaffolding at sunset" style="top:2429px;background:radial-gradient(ellipse 100px 60px at 50px 30px,#fde6bd,rgba(253,230,189,0) 100%),radial-gradient(ellipse 30px 60px at 180px 110px,rgba(220,90,30,.85),rgba(220,90,30,0) 100%),linear-gradient(120deg,#eab477,#8d6b52 55%,#4a3c32)"></div>
<article class="post-card" style="top:2442px"><h4>NEMO ENIM IPSAM VOLUP</h4><div class="post-meta"><span>▦ Jan 25, 2020</span><span>◌ 2 comments</span></div><p>Sed ut perspiciatis unde omnis iste natus error sit vuptatem aum doloremque</p></article>

<div class="post-photo" role="img" aria-label="Photo of two engineers in orange vests with a crane behind them" style="top:2612px;background:radial-gradient(ellipse 70px 50px at 100px 130px,rgba(235,110,40,.95),rgba(235,110,40,0) 100%),linear-gradient(170deg,#2c6fc0 0%,#5d93cc 40%,#8a8f8f 70%,#4f4a44 100%)"></div>
<article class="post-card" style="top:2626px"><h4>NEMO ENIM IPSAM VOLUP</h4><div class="post-meta"><span>▦ Jan 25, 2020</span><span>◌ 2 comments</span></div><p>Sed ut perspiciatis unde omnis iste natus error sit vuptatem aum doloremque</p></article>

<div class="quote-bg" role="img" aria-label="Faint grey construction skyline with cranes"></div>
<form class="quote">
  <h2>REQUEST A QUOTE</h2>
  <div class="field" style="top:105px">Name</div>
  <div class="field" style="top:161px">Contact Email</div>
  <div class="field" style="top:217px">Contact Phone</div>
  <div class="field" style="top:274px">upload photos<span class="upload">UPLOAD</span></div>
  <div class="field" style="top:329px;height:94px">Message</div>
  <div class="btn" style="left:103px;top:449px;width:166px;height:37px;font-size:14px">Get Quotes <svg viewBox="0 0 16 16"><path d="M2 8h11M9 4l4 4-4 4" stroke="#fff" stroke-width="2" fill="none"/></svg></div>
</form>

<!-- team -->
<section class="team">
  <div class="team-photo" role="img" aria-label="Overhead photo of engineers in hard hats working over construction plans on a concrete floor"></div>
</section>
<svg class="abs" style="left:0;top:2862px" width="1200" height="90"><polyline points="0,86 600,4 1200,86" fill="none" stroke="var(--blue-dark)" stroke-width="4"/></svg>
<svg class="abs" style="left:0;top:3463px" width="1200" height="92"><polyline points="0,4 600,87 1200,4" fill="none" stroke="var(--blue-dark)" stroke-width="4"/></svg>
<div class="role" style="left:572px;top:3062px"><div class="ico" role="img" aria-label="Icon of a manager"></div>Managing<br>Director</div>
<div class="role" style="left:740px;top:3062px"><div class="ico" role="img" aria-label="Icon of a director"></div>Contract<br>Director</div>
<div class="role" style="left:907px;top:3062px;padding-top:26px"><div class="ico" role="img" aria-label="Icon of an estimator"></div>Estimator</div>
<div class="role" style="left:572px;top:3238px"><div class="ico" role="img" aria-label="Icon of a finance officer"></div>Senior<br>Financial Officer</div>
<div class="role" style="left:740px;top:3238px"><div class="ico" role="img" aria-label="Icon of an administrator"></div>Contracts<br>Administrator</div>
<div class="role" style="left:907px;top:3238px"><div class="ico" role="img" aria-label="Icon of a safety manager"></div>Safety<br>Manager</div>

<!-- projects -->
<h2 class="section-title" style="top:3624px;color:#222"><b>OUR</b> <span>PROJECTS</span></h2>
<div class="abs" style="left:570px;top:3685px;width:60px;height:3px;background:var(--blue)"></div>
<div class="site-fade" role="img" aria-label="Faint grey construction site with machinery"></div>
<div class="proj" role="img" aria-label="Photo of two engineers in hi-vis jackets with a laptop" style="left:144px;top:3744px;background:radial-gradient(ellipse 70px 90px at 70px 170px,rgba(200,220,60,.9),rgba(200,220,60,0) 100%),radial-gradient(ellipse 70px 90px at 200px 180px,rgba(235,120,50,.9),rgba(235,120,50,0) 100%),linear-gradient(180deg,#e6e6e3,#cfcfcb)"></div>
<div class="proj" role="img" aria-label="Photo of construction plans on a desk" style="left:451px;top:3744px;background:linear-gradient(135deg,#9bb4cc,#607c98)"></div>
<div class="proj" role="img" aria-label="Photo of two workers at a building site" style="left:757px;top:3744px;background:radial-gradient(ellipse 60px 100px at 110px 170px,rgba(70,70,75,.8),rgba(70,70,75,0) 100%),linear-gradient(160deg,#f2dfc0,#c9a47a 50%,#8a7564)"></div>
<div class="proj" role="img" aria-label="Photo of a crane lifting steel beams" style="left:144px;top:4016px;background:radial-gradient(ellipse 120px 40px at 150px 70px,rgba(225,120,40,.8),rgba(225,120,40,0) 100%),linear-gradient(180deg,#d3dbe2,#8f9aa3 60%,#5e666c)"></div>
<div class="proj" role="img" aria-label="Photo of hands over a blueprint with a hard hat" style="left:451px;top:4016px;background:radial-gradient(ellipse 70px 70px at 230px 190px,rgba(220,100,40,.9),rgba(220,100,40,0) 100%),linear-gradient(135deg,#3e3e3e,#8a8a88 55%,#c9c6c2)"></div>
<div class="proj" role="img" aria-label="Photo of workers tying rebar" style="left:757px;top:4016px;background:radial-gradient(ellipse 60px 80px at 140px 90px,rgba(200,50,40,.75),rgba(200,50,40,0) 100%),linear-gradient(135deg,#3e4a58,#6b7480 50%,#4b4036)"></div>
<div class="proj-hover"><h4>Construction Plan</h4><p>Sed ut perspiciatis unde omnis iste natus error sit voluptatem accusantium doloremque laudantium</p></div>

<!-- footer -->
<footer class="footer"></footer>
<svg class="abs" style="left:0;top:4446px" width="1200" height="90"><polyline points="0,86 600,4 1200,86" fill="none" stroke="var(--blue)" stroke-width="5"/></svg>
<h3 class="foot-h" style="left:143px">CONTACT US</h3>
<h3 class="foot-h" style="left:466px;font-size:21px;top:4558px">SIGN UP TO RECEIVE EMAIL</h3>
<h3 class="foot-h" style="left:905px">QUICK LINKS</h3>

<svg class="abs" style="left:145px;top:4614px" width="14" height="18" viewBox="0 0 14 18"><path d="M7 1a6 6 0 00-6 6c0 4.5 6 10 6 10s6-5.5 6-10a6 6 0 00-6-6z" fill="none" stroke="#ccc" stroke-width="1.4"/><circle cx="7" cy="7" r="2" fill="none" stroke="#ccc" stroke-width="1.4"/></svg>
<p class="foot-t" style="left:180px;top:4612px">BRINDLEWORK<br>Unit 9, Larkfield Centre<br>Harrowdale 4410</p>
<svg class="abs" style="left:144px;top:4683px" width="16" height="16" viewBox="0 0 24 24"><path fill="none" stroke="#ccc" stroke-width="1.6" d="M6.6 10.8a15 15 0 006.6 6.6l2.2-2.2c.3-.3.7-.4 1-.2 1.1.4 2.3.6 3.6.6.6 0 1 .4 1 1V20c0 .6-.4 1-1 1A17 17 0 013 4c0-.6.4-1 1-1h3.5c.6 0 1 .4 1 1 0 1.3.2 2.5.6 3.6.1.3 0 .7-.2 1z"/></svg>
<p class="foot-t" style="left:180px;top:4680px">Phone : +808 55 012 4471<br>Fax : 808 55 012 4472</p>
<svg class="abs" style="left:144px;top:4744px" width="18" height="13" viewBox="0 0 18 13"><rect x="1" y="1" width="16" height="11" fill="none" stroke="#ccc" stroke-width="1.3"/><path d="M1 1l8 6 8-6" fill="none" stroke="#ccc" stroke-width="1.3"/></svg>
<p class="foot-t" style="left:180px;top:4740px">Email : info@brindlework.com</p>

<p class="foot-t" style="left:466px;top:4610px;width:330px">Excepteur sint occaecat cupidatat non proident, sunt in culpa qui Nemo enim ipsam voluptatem</p>
<div class="subscribe">Enter Email<span>SUBSCRIBE</span></div>
<div class="social" style="left:474px"></div>
<div class="social" style="left:505px"></div>
<div class="social" style="left:536px"></div>
<div class="social" style="left:567px"></div>

<ul class="foot-links"><li>Home</li><li>About Us</li><li>Our Services</li><li>Projects</li><li>Blog</li><li>Contact</li></ul>
<p class="copy">Copyright © BRINDLEWORK 2020. All rights reserved. | Privacy Policy</p>

</body>
</html>
```